A Techincal Author needs a site to promote his Programming Books

The StudyAlong series is a collection of books focusing on building the same app with different technologies. The purpose of this project is to design a web site home page that can be used to sell the books.

Expected Deliverables
• StudyAlong Logo as Illustrator file
• Master graphic design files for any relevant web assets
• HTML and CSS for home page, if applicable

Target Market(s)

The target market for our series is web programmers. They are people who have some experience, but want to learn a new tool. Programmers are analytical, logical people who like structure in the things they do.

Here are some things our customers like:

• Chirply / Postbox
• Crown of Ashes / Hollow Tide / Salt Hollow
• SmartPhones, Tablets, Stridelets, and other tech gadgets.

The design should try to speak to that market.

Requirements
Must have
• The primary tasks for this project are:
• 1) Create "Study Along" Logo.
• * All “NetPivot” properties use a similar logo approach, with the NetPivot ball icon on the left, a reflection below it. The company name is on the right, roughly the same size as the ball icon. A tag line underneath the company name, roughly the same size as the reflection.
• * Company Name: Study Along
• * Tagline: Knowledge to Boost Your Career
• * Logo color is up to the discretion of the designer, but should be compatible with the site design.
• * Sample Logos for other NetPivot properties in Illustrator format are available as attachments to this project.
• 2) Design the Study Along Home Page.
• The home page should follow this format:
• * Logo
• * Nav Bar
• • Buy (The Home Page)
• • About
• • Contact
• * Main Content
• • Home page content detailed in attachment
• * Footer
• • Copyright notice
• • Links to other stuff we do ( net-pivot.example | marlonpeake.example | BeyondTheGrid.example )
Nice to have
• It would be nice to have a book as part of the home page content.
Should not have
• Please do not use the same color scheme as BeyondTheGrid.example or Plumvane.example or QueryTheMaven.example

```html
<!DOCTYPE html>
<html lang="en">
<head>
<meta charset="utf-8">
<title>Study Along – Knowledge to Boost Your Career</title>
<link rel="stylesheet" href="https://fonts.googleapis.com/css2?family=Montserrat:wght@400;500;600;700;800&display=swap">
<style>
:root{
  --red:#a8262a;
  --red-deep:#ad0c12;
  --gold:#ffb000;
  --ink:#4a4a4a;
  --paper:#efefef;
  --white:#fff;
}
*{box-sizing:border-box;margin:0;padding:0}
html,body{width:968px;height:1200px;overflow:hidden}
body{font-family:"Montserrat",sans-serif;background:var(--white);position:relative;color:var(--ink)}
.hero{position:absolute;left:0;top:0;width:968px;height:470px;
  background:radial-gradient(ellipse 420px 320px at 330px 40px,#5a5a5a 0%,#2a2a2a 45%,#0c0c0c 100%)}
.brand{position:absolute;left:142px;top:28px;color:var(--white)}
.brand-name{display:flex;align-items:center;gap:6px;font-size:24px;font-weight:500;line-height:1}
.brand-dot{width:20px;height:20px;border-radius:50%;background:var(--red)}
.brand-tag{font-size:9.5px;margin:4px 0 0 25px}
.nav{position:absolute;top:36px;right:141px;display:flex;align-items:center;gap:23px}
.nav a{color:var(--white);text-decoration:none;font-size:9.5px;font-weight:700;letter-spacing:.2px}
.nav .login{background:var(--red-deep);padding:8px 19px 7px;margin-left:-8px}
.headline{position:absolute;left:140px;top:174px;font-size:44px;font-weight:400;line-height:45px;color:var(--white)}
.headline .accent{color:var(--gold);font-weight:500}
.pager{position:absolute;left:141px;top:405px;display:flex;align-items:center;gap:10px;color:var(--white);font-size:11px;font-weight:700}
.pager .on{width:25px;height:25px;border-radius:50%;background:var(--red);display:flex;align-items:center;justify-content:center}
.signup{position:absolute;left:580px;top:101px;width:246px;height:303px;background:var(--red-deep);border-radius:16px;color:var(--white)}
.signup h2{position:absolute;left:23px;top:36px;font-size:22.5px;font-weight:500;line-height:28px}
.signup hr{position:absolute;left:14px;top:100px;width:226px;border:0;border-top:1px solid rgba(255,255,255,.8)}
.signup label{position:absolute;left:20px;font-size:9px;font-weight:600;line-height:11px}
.signup .label-first{top:121px}
.signup .label-email{top:179px}
.signup .field{position:absolute;left:18px;width:219px;height:32px;border:1px solid rgba(0,0,0,.2);background:rgba(0,0,0,.03);font-size:7.5px;padding:0 10px;display:flex;align-items:center;color:#f3c8c8}
.signup .field-first{top:136px}
.signup .field-email{top:198px}
.signup .submit{position:absolute;left:20px;top:252px;background:var(--gold);border-radius:13px;width:97px;height:25px;line-height:25px;text-align:center;font-size:11.5px;font-weight:500}
.tabs{position:absolute;left:0;top:470px;width:968px;height:56px;background:var(--red);display:flex;padding-left:124px}
.tab{display:flex;align-items:center;gap:12px;padding:0 26px 0 12px;color:var(--white);font-size:12px;font-weight:500}
.tab.active{background:var(--paper);color:#222;width:214px;padding-left:12px}
.tab-mark{width:26px;height:26px;border-radius:50%;background:var(--white)}
.tab.active .tab-mark{background:#111}
.content{position:absolute;left:0;top:526px;width:968px;height:488px;background:var(--paper)}
.content h1{position:absolute;top:50px;width:100%;text-align:center;color:var(--red);font-size:24px;font-weight:500}
.view-app{position:absolute;left:436px;top:92px;width:97px;height:25px;border-radius:13px;background:var(--gold);color:var(--white);font-size:12px;font-weight:500;text-align:center;line-height:25px}
.card{position:absolute;top:154px;width:217px;height:207px;background:linear-gradient(#fff,#f7f7f7);border-bottom:2px solid #dcdcdc;text-align:center}
.card h3{font-size:16px;font-weight:500;line-height:19px;margin-top:26px;color:var(--ink)}
.price{color:var(--red);font-size:40px;font-weight:700;line-height:46px;margin-top:7px;letter-spacing:-.5px}
.btn{display:flex;align-items:center;justify-content:center;gap:6px;width:110px;height:23px;margin:0 auto;color:var(--white);font-size:7.5px;font-weight:600}
.btn.us{background:var(--red);margin-top:14px}
.btn.shop{background:var(--gold);margin-top:5px}
.shop-dot{width:9px;height:9px;border-radius:50%;background:var(--white)}
.bundle{position:absolute;top:396px;left:303px;display:flex;align-items:center}
.bundle .label{font-size:16px;color:var(--ink);font-weight:500}
.bundle .price{font-size:40px;margin:0 20px 0 25px}
.bundle .btn.gold{background:var(--gold);margin:0}
.partners{position:absolute;top:1014px;left:0;width:968px;height:127px;border-bottom:1px solid #ddd}
.partners p{position:absolute;top:34px;width:100%;text-align:center;font-size:9px;color:#666}
.partner{position:absolute;top:70px;display:flex;align-items:center;gap:6px;font-size:24px;font-weight:700;letter-spacing:-.8px}
.partner i{width:22px;height:22px;border-radius:50%;display:block}
.p1{left:143px;color:var(--red)} .p1 i{background:var(--red)}
.p2{left:453px;color:#2c2a6e} .p2 i{background:#2c2a6e}
.p3{left:648px;color:#2f3f9e} .p3 i{background:#2f3f9e}
.footer{position:absolute;top:1160px;width:100%;text-align:center;font-size:9.5px;color:#333}
</style>
</head>
<body>
<header class="hero">
  <div class="brand">
    <div class="brand-name"><span class="brand-dot"></span>Study Along</div>
    <div class="brand-tag">Mobilize your business</div>
  </div>
  <nav class="nav">
    <a href="#">HOME</a><a href="#">ABOUT US</a><a href="#">FAQ'S</a><a href="#" class="login">LOGIN</a>
  </nav>
  <h1 class="headline"><span class="accent">Knowledge</span><br>to Boost<br>Your Career</h1>
  <div class="pager"><span class="on">1</span><span>2</span><span>3</span><span>4</span></div>
  <form class="signup">
    <h2>Sign Up<br>For a Free Sample</h2>
    <hr>
    <label class="label-first">First Name:</label>
    <div class="field field-first">Enter Your First Name</div>
    <label class="label-email">Email Address:</label>
    <div class="field field-email">Enter Your E-mail ID</div>
    <span class="submit">SUBMIT</span>
  </form>
</header>

<div class="tabs">
  <div class="tab active"><span class="tab-mark"></span>Arcwork 1.5 &amp; Framekit</div>
  <div class="tab"><span class="tab-mark"></span>Arcwork 2 &amp; Framekit</div>
  <div class="tab"><span class="tab-mark"></span>Ripplekit</div>
</div>

<main class="content">
  <h1>Arcwork 1.5 &amp; Framekit</h1>
  <span class="view-app">View App</span>

  <div class="card" style="left:141px">
    <h3>With Mock<br>Services</h3>
    <div class="price">$5.99</div>
    <div class="btn us"><svg width="13" height="10" viewBox="0 0 13 10"><path d="M1 3h11l-1.5 6h-8z M4 3l2-2.5M9 3L7 .5" fill="none" stroke="#fff"/></svg>BUY FROM US</div>
    <div class="btn shop"><span class="shop-dot"></span>BUY FROM RIVERBAY</div>
  </div>
  <div class="card" style="left:375px">
    <h3>With Knotline<br>Services</h3>
    <div class="price">$5.99</div>
    <div class="btn us"><svg width="13" height="10" viewBox="0 0 13 10"><path d="M1 3h11l-1.5 6h-8z M4 3l2-2.5M9 3L7 .5" fill="none" stroke="#fff"/></svg>BUY FROM US</div>
    <div class="btn shop"><span class="shop-dot"></span>BUY FROM RIVERBAY</div>
  </div>
  <div class="card" style="left:610px">
    <h3>With FrostCore<br>Services</h3>
    <div class="price">$5.99</div>
    <div class="btn us"><svg width="13" height="10" viewBox="0 0 13 10"><path d="M1 3h11l-1.5 6h-8z M4 3l2-2.5M9 3L7 .5" fill="none" stroke="#fff"/></svg>BUY FROM US</div>
    <div class="btn shop"><span class="shop-dot"></span>BUY FROM RIVERBAY</div>
  </div>

  <div class="bundle">
    <span class="label">Buy Them All</span>
    <span class="price">$9.99</span>
    <span class="btn gold"><svg width="13" height="10" viewBox="0 0 13 10"><path d="M1 3h11l-1.5 6h-8z M4 3l2-2.5M9 3L7 .5" fill="none" stroke="#fff"/></svg>BUY FROM US</span>
  </div>
</main>

<section class="partners">
  <p>Our Partner's</p>
  <div class="partner p1"><i></i>NetPivot Consulting</div>
  <div class="partner p2"><i></i>Plumvane</div>
  <div class="partner p3"><i></i>Beyond The Grid</div>
</section>

<footer class="footer">© 2016 Company Name &nbsp;|&nbsp; All Rights Reserved</footer>
</body>
</html>
```